Tidal Forge - Crypto Currency Miner Powered by Renewable Energy Website

We Need Web Pages Design for Website for Crypto Currency Miner

Serivices include:
Mining Rig Sales
Housing for Rigs turnkey on renewable energy grid
Cloud Mining term packages
Updates

http://www.vaultrigsurvey.example (Competitors sites)

Target Market(s)

Investers for Mining Rigs and terms for 1,2 or 3 years of Hash rate

Industry/Entity Type

Mining

Number of Pages Required

5+ page

Font styles to use
Sans Serif

Colors
add136
9bcb3c
606060
474747
ffc214
cadf82
fbee3e
876aae
6b449b

Requirements
Must have
• Pictures of Solar, Wind and power Factor Correction units
Nice to have
• e-commerce platform so contract terms can be purchased through website
Should not have
• Heavy construction equipment

```html
<!DOCTYPE html>
<html lang="en">
<head>
<meta charset="utf-8">
<title>Tidal Forge — Crypto Currency Miner</title>
<link href="https://fonts.googleapis.com/css2?family=Roboto+Condensed:wght@300;400;700&family=Roboto:wght@400;500&display=swap" rel="stylesheet">
<style>
:root{
  --canvas:#ececec;
  --lime:#add136;
  --leaf:#9bcb3c;
  --forest:#0e9a48;
  --meadow:#45a85a;
  --meadow-light:#58b56a;
  --ink:#474747;
  --grey:#606060;
  --amber:#ffc214;
  --lemon:#fbee3e;
  --pale:#cadf82;
  --white:#ffffff;
  --dark-btn:#2f2f2f;
}
*{margin:0;padding:0;box-sizing:border-box}
html,body{width:1200px;height:1200px;overflow:hidden;background:var(--canvas)}
body{font-family:"Roboto Condensed",sans-serif;color:var(--ink);position:relative}
.page{position:absolute;left:336px;top:34px;width:529px;height:1166px;background:var(--white);box-shadow:0 0 14px rgba(0,0,0,.08);overflow:hidden}
.abs{position:absolute}

.top-strip{left:0;top:0;width:100%;height:5px;background:linear-gradient(90deg,var(--lime),var(--forest))}
.nav{left:0;top:5px;width:100%;height:29px;background:var(--white)}
.nav a{position:absolute;top:12px;font:500 5.5px "Roboto",sans-serif;letter-spacing:.4px;color:var(--grey);text-decoration:none}
.nav .active-tab{position:absolute;left:239px;top:0;width:37px;height:23px;background:var(--amber)}
.nav .active-tab span{position:absolute;left:0;right:0;top:12px;text-align:center;font:500 5.5px "Roboto",sans-serif;color:var(--ink);letter-spacing:.4px}

.hero{left:0;top:34px;width:100%;height:390px}
.hero-art{position:absolute;inset:0;background:
  radial-gradient(ellipse 110px 110px at 145px 145px,#cfe9a6 0%,#79c04a 55%,rgba(120,190,70,0) 100%),
  radial-gradient(ellipse 220px 140px at 350px 60px,#f4fbe6 0%,rgba(230,245,200,0) 100%),
  linear-gradient(180deg,#9ed35c 0%,#b9e07f 45%,#8fcc44 72%,#5fb33a 100%)}
.hero-wave{position:absolute;left:0;bottom:0;width:100%;height:120px}
.logo-tab{left:86px;top:6px;width:90px;height:68px;background:var(--white);z-index:2}
.logo-tab .dot{position:absolute;left:38px;top:16px;width:15px;height:15px;border-radius:50%;background:var(--leaf)}
.logo-tab .name{position:absolute;left:0;right:0;top:42px;text-align:center;font:400 14px "Roboto Condensed",sans-serif;color:var(--grey)}
.hero-tagline{left:92px;top:111px;width:112px;font:400 7px/9px "Roboto Condensed",sans-serif;color:var(--white)}
.hero-title{left:256px;top:58px;width:212px;text-align:center;font:400 36px/35px "Roboto Condensed",sans-serif;color:var(--ink);text-transform:uppercase;letter-spacing:-1px;white-space:nowrap}
.btn-dark{left:325px;top:176px;width:92px;height:20px;background:var(--dark-btn);border-radius:2px;color:var(--white);font:400 10px/20px "Roboto Condensed",sans-serif;text-align:center}

.login-card{left:70px;top:233px;width:84px;height:135px;border-radius:8px;background:linear-gradient(180deg,#ffd22e,var(--amber));box-shadow:0 2px 6px rgba(0,0,0,.15)}
.login-card .badge{position:absolute;left:21px;top:-22px;width:42px;height:42px;border-radius:50%;background:var(--white);border:3px solid var(--leaf)}
.login-card .field{position:absolute;left:9px;width:65px;height:13px;border-radius:7px;background:var(--white);font:400 4.5px/13px "Roboto",sans-serif;color:#bbb;padding-left:15px;letter-spacing:.3px}
.login-card .field i{position:absolute;left:6px;top:4px;width:5px;height:5px;background:var(--grey);border-radius:1px}
.login-card .remember{position:absolute;left:20px;top:94px;font:400 4px "Roboto",sans-serif;color:var(--white)}
.login-card .remember::before{content:"";position:absolute;left:-7px;top:0;width:4px;height:4px;border-radius:50%;background:var(--ink)}
.login-card .login-btn{position:absolute;left:23px;top:106px;width:38px;height:13px;border-radius:7px;background:#ffe37a;font:400 5px/13px "Roboto",sans-serif;color:var(--white);text-align:center;letter-spacing:.3px}
.login-card .register{position:absolute;left:0;right:0;top:125px;text-align:center;font:400 3.5px "Roboto",sans-serif;color:var(--white)}
.login-card .register b{color:var(--ink);font-weight:500}

.feature{width:97px;top:448px}
.feature .tile{width:97px;height:97px;background:linear-gradient(135deg,#a7d34a,var(--leaf) 60%,#92c437);display:flex;align-items:center;justify-content:center}
.feature h3{margin-top:10px;text-align:center;font:300 12px/14px "Roboto Condensed",sans-serif;color:var(--leaf);text-transform:uppercase}
.feature p{margin:9px auto 0;width:88px;text-align:center;font:400 5.6px/7.2px "Roboto Condensed",sans-serif;color:var(--ink)}
.feature .btn-outline{display:block;margin:7px auto 0;width:55px;height:13px;border:1px solid var(--pale);border-radius:2px;text-align:center;font:400 6px/11px "Roboto Condensed",sans-serif;color:var(--ink)}

.band-market{left:0;top:658px;width:100%;height:251px;background:var(--forest)}
.band-why{left:0;top:909px;width:100%;height:257px;background:var(--meadow)}
.band-foot{left:0;top:1159px;width:100%;height:7px;background:var(--meadow-light)}

.section-title{left:78px;font:400 20px/22px "Roboto Condensed",sans-serif;color:var(--white);letter-spacing:-.5px;white-space:nowrap}
.section-title--why{font-size:18px;letter-spacing:-.6px}
.lead{left:78px;width:152px;font:400 8.8px/10px "Roboto Condensed",sans-serif;color:var(--white);text-align:justify}
.fine{left:78px;width:152px;font:400 5.2px/7px "Roboto Condensed",sans-serif;color:var(--white);text-align:justify}
.btn-ghost{left:175px;width:55px;height:12px;border:1px solid var(--white);border-radius:2px;color:var(--white);font:400 6px/10px "Roboto Condensed",sans-serif;text-align:center}

.laptop{left:248px;top:744px;width:238px;height:162px}
.laptop .frame{position:absolute;left:10px;top:0;width:218px;height:157px;border-radius:7px;background:#c9c9c9;border:1px solid #e4e4e4}
.laptop .screen{position:absolute;left:21px;top:12px;width:196px;height:134px;background:linear-gradient(180deg,#c6e07c 0%,#9fce54 55%,#78b838 100%)}
.laptop .base{position:absolute;left:0;top:155px;width:238px;height:5px;border-radius:0 0 6px 6px;background:linear-gradient(180deg,#e6e6e6,#a9a9a9)}

.perk{width:81px;height:81px;border-radius:3px;display:flex;flex-direction:column;align-items:center;justify-content:flex-end;padding-bottom:9px;font:400 11px/12px "Roboto Condensed",sans-serif;text-align:center}
.perk svg{margin-bottom:auto;margin-top:13px}
.perk--leaf{background:var(--leaf);color:var(--white);border:2px solid #b7dd66}
.perk--amber{background:var(--amber);color:var(--white)}
.perk--lemon{background:var(--lemon);color:var(--ink)}
.perk--white{background:var(--white);color:var(--ink)}
</style>
</head>
<body>
<main class="page">
  <div class="abs top-strip"></div>
  <nav class="abs nav">
    <a style="left:210px">HOME</a>
    <div class="active-tab"><span>PRICING</span></div>
    <a style="left:293px">OUR OFFER</a>
    <a style="left:341px">ABOUT US</a>
    <a style="left:388px">CUSTOMER SERVICE</a>
  </nav>

  <section class="abs hero">
    <div class="hero-art" role="img" aria-label="Green globe plugged into a power cable above flowing green waves"></div>
    <svg class="hero-wave" viewBox="0 0 529 120" preserveAspectRatio="none">
      <path d="M0 95 C90 60 170 120 270 88 C360 60 450 40 529 70 L529 120 L0 120 Z" fill="#ffffff"/>
    </svg>
  </section>

  <div class="abs logo-tab">
    <span class="dot"></span>
    <span class="name">Tidal Forge</span>
  </div>

  <p class="abs hero-tagline">Join over 1,000 people with the world's leading mining service.</p>
  <h1 class="abs hero-title">Start<br>Tidal Forge<br>Today!</h1>
  <div class="abs btn-dark">Learn More</div>

  <form class="abs login-card">
    <span class="badge"></span>
    <div class="field" style="top:59px"><i></i>USERNAME</div>
    <div class="field" style="top:78px"><i></i>PASSWORD</div>
    <span class="remember">Remember Me ?</span>
    <div class="login-btn">LOG IN</div>
    <span class="register">Don't have a account? <b>REGISTER HERE</b></span>
  </form>

  <article class="abs feature" style="left:98px">
    <div class="tile">
      <svg width="30" height="30" viewBox="0 0 30 30" fill="none" stroke="#fff" stroke-width="1.1">
        <circle cx="15" cy="15" r="13" stroke-dasharray="3 2"/>
        <circle cx="15" cy="15" r="2"/>
        <path d="M15 13 L13 4 Q15 2 17 4 Z M16.8 16 L25 19 Q25 22 22 22 Z M13.2 16 L7 23 Q5 21 6 19 Z"/>
      </svg>
    </div>
    <h3>Wind Power<br>Investment</h3>
    <p>Don't wrestle with rig assembly and hot, noisy miners at home. We have the fastest bitcoin mining hardware running for you already!</p>
    <span class="btn-outline">Learn More</span>
  </article>
  <article class="abs feature" style="left:216px">
    <div class="tile">
      <svg width="32" height="30" viewBox="0 0 32 30" fill="none" stroke="#fff" stroke-width="1.1">
        <circle cx="17" cy="4" r="2"/>
        <rect x="3" y="9" width="26" height="14"/>
        <path d="M3 14H29M3 18.5H29M9.5 9V23M16 9V23M22.5 9V23M16 23V28M11 28H21"/>
      </svg>
    </div>
    <h3>Solar Power<br>Investment</h3>
    <p>Don't wrestle with rig assembly and hot, noisy miners at home. We have the fastest bitcoin mining hardware running for you already!</p>
    <span class="btn-outline">Learn More</span>
  </article>
  <article class="abs feature" style="left:334px">
    <div class="tile">
      <svg width="32" height="30" viewBox="0 0 32 30" fill="none" stroke="#fff" stroke-width="1.1">
        <path d="M6 10 L18 3 L22 10 M12 10 L22 5 L25 10"/>
        <rect x="3" y="10" width="26" height="17" rx="2"/>
        <rect x="21" y="15" width="9" height="7" rx="1"/>
        <circle cx="24" cy="18.5" r="1"/>
      </svg>
    </div>
    <h3>Get Your First<br>Payout Today</h3>
    <p>Don't wrestle with rig assembly and hot, noisy miners at home. We have the fastest bitcoin mining hardware running for you already!</p>
    <span class="btn-outline">Learn More</span>
  </article>

  <section class="abs band-market"></section>
  <h2 class="abs section-title" style="top:686px">Buy And Sell<br>Crypto Currency Miner</h2>
  <p class="abs lead" style="top:740px">Lorem ipsum dolor sit amet, consectetur adipisicing elit. Aliquam praesentium, distinctio dicta molestias dignissimos.</p>
  <p class="abs fine" style="top:776px">Lorem ipsum dolor sit amet, consectetur adipisicing elit. Quam earum, provident ad, porro aperiam dolore, blanditiis, nihil pariatur eius adipisci consequuntur officiis. Excepturi, nostrum? Id incidunt nesciunt officia hic distinctio nihil pariatur.</p>
  <p class="abs fine" style="top:812px">Lorem ipsum dolor sit amet, consectetur adipisicing elit. Quam earum, provident ad, porro aperiam dolore, blanditiis, nihil pariatur eius adipisci consequuntur officiis. Excepturi, nostrum? Id incidunt nesciunt officia hic distinctio nihil pariatur. Lorem ipsum dolor sit amet, consectetur adipisicing elit. Quam earum, provident ad, porro aperiam dolore, blanditiis, nihil pariatur eius adipisci consequuntur officiis.</p>
  <div class="abs btn-ghost" style="top:874px">Learn More</div>

  <div class="abs laptop">
    <div class="frame"></div>
    <div class="screen" role="img" aria-label="Laptop screen showing the Tidal Forge home page with a wind turbine scene"></div>
    <div class="base"></div>
  </div>

  <section class="abs band-why"></section>
  <div class="abs band-foot"></div>
  <h2 class="abs section-title section-title--why" style="top:953px">Why Choose Tidal Forge?</h2>
  <p class="abs lead" style="top:982px">Lorem ipsum dolor sit amet, consectetur adipisicing elit. Aliquam praesentium, distinctio dicta molestias dignissimos.</p>
  <p class="abs fine" style="top:1019px">Lorem ipsum dolor sit amet, consectetur adipisicing elit. Quam earum, provident ad, porro aperiam dolore, blanditiis, nihil pariatur eius adipisci consequuntur officiis. Excepturi, nostrum? Id incidunt nesciunt officia hic distinctio nihil pariatur.</p>
  <p class="abs fine" style="top:1054px">Lorem ipsum dolor sit amet, consectetur adipisicing elit. Quam earum, provident ad, porro aperiam dolore, blanditiis, nihil pariatur eius adipisci consequuntur officiis. Excepturi, nostrum? Id incidunt nesciunt officia hic distinctio nihil pariatur. Lorem ipsum dolor sit amet, consectetur adipisicing elit. Quam earum, provident ad, porro aperiam dolore, blanditiis, nihil pariatur eius adipisci consequuntur officiis.</p>
  <div class="abs btn-ghost" style="top:1118px">Learn More</div>

  <div class="abs perk perk--leaf" style="left:259px;top:944px">
    <svg width="30" height="34" viewBox="0 0 30 34" fill="none" stroke="#fff" stroke-width="1.3">
      <path d="M15 2 L27 6 V16 C27 24 21 29 15 32 C9 29 3 24 3 16 V6 Z"/>
      <path d="M15 6 L23 9 V16 C23 22 19 25 15 27 C11 25 7 22 7 16 V9 Z"/>
      <circle cx="15" cy="14" r="3"/><path d="M15 17 V22"/>
    </svg>
    Safe And Secure
  </div>
  <div class="abs perk perk--amber" style="left:359px;top:944px">
    <svg width="36" height="34" viewBox="0 0 36 34" fill="none" stroke="#fff" stroke-width="1.3">
      <rect x="4" y="2" width="16" height="30" rx="2"/><path d="M10 28H14"/>
      <circle cx="27" cy="19" r="5" stroke-dasharray="2.5 1.5"/><circle cx="27" cy="19" r="2"/>
      <circle cx="12" cy="12" r="4" stroke-dasharray="2 1.5"/>
    </svg>
    Mobile App
  </div>
  <div class="abs perk perk--lemon" style="left:259px;top:1039px">
    <svg width="36" height="32" viewBox="0 0 36 32" fill="none" stroke="#474747" stroke-width="1.3">
      <rect x="6" y="3" width="26" height="22" rx="2"/>
      <path d="M6 9H32"/><rect x="25" y="12" width="9" height="7" rx="1"/>
      <path d="M3 16 L10 14 L16 16 V22 C16 26 13 28 10 30 C7 28 3 26 3 22 Z" fill="#fbee3e"/>
      <path d="M6.5 21 L9 23.5 L13 19"/>
    </svg>
    Secure Wallet
  </div>
  <div class="abs perk perk--white" style="left:359px;top:1039px">
    <svg width="34" height="34" viewBox="0 0 34 34" fill="none" stroke="#474747" stroke-width="1.3">
      <rect x="5" y="4" width="20" height="26" rx="1"/><rect x="11" y="2" width="8" height="4"/>
      <path d="M15 10 L21 12 V17 C21 21 18 23 15 24 C12 23 9 21 9 17 V12 Z"/>
      <circle cx="26" cy="26" r="5" fill="#fff"/><path d="M26 23 V29 M23 26 H29"/>
    </svg>
    Covered By<br>Insurance
  </div>
</main>
</body>
</html>
```